Stationary design for boutique production house

We need a stationary design for our production house, 'Lorno Productions' based in Singapore. We produce microfilms as well as podcasts, talkshows and events. Our logo is a stylized icon of our director, who is also the executive producer and host of our programs, Lorno. Our main company colors are Red, Black and white. We would like a clean, minimalist design incorporating our existing company logo that conveys a sense of urbanism and elegance.

Logo and font files are attached. f

Target Market(s)

We focus on lifestyle media rather than entertainment.

Industry/Entity Type

Boutique

Font styles to use
Serif
Sans Serif

Colors
ec1f27
ffffff
000000

Requirements
Must have
• Our company logo and at least one of our company colors.
Nice to have
• Our address and contact information.
Should not have
• Changes made to the company logo (using only certain parts of it is fine though)

```html
<!DOCTYPE html>
<html lang="en">
<head>
<meta charset="utf-8">
<title>Lorno Productions – Business Card</title>
<link rel="stylesheet" href="https://fonts.googleapis.com/css2?family=Noto+Serif:wght@400;700&display=swap">
<style>
  :root {
    --stage: #2e2e2e;
    --card-dark: #1f1c1d;
    --pattern-a: #2a2627;
    --pattern-b: #353032;
    --paper: #f7f7f5;
    --ink: #1b1b1b;
    --ink-soft: #4a4a4a;
    --brand-red: #ec1f27;
    --white: #ffffff;
  }
  * { box-sizing: border-box; margin: 0; padding: 0; }
  html, body {
    width: 1200px; height: 768px; overflow: hidden;
    background: var(--stage);
    font-family: "Noto Serif", Georgia, serif;
  }
  .stage {
    position: relative; width: 1200px; height: 768px;
    display: flex; align-items: center; justify-content: center; gap: 60px;
  }
  .card {
    position: relative; width: 520px; height: 297px; overflow: hidden;
    box-shadow: 0 14px 30px rgba(0,0,0,.45);
  }

  /* Back side */
  .card--back { background: var(--card-dark); }
  .back-pattern {
    position: absolute; inset: 0;
    background: linear-gradient(135deg, var(--pattern-b) 0%, var(--pattern-a) 55%, var(--card-dark) 100%);
  }
  .back-brand {
    position: absolute; right: 40px; top: 118px;
    display: flex; align-items: center; gap: 10px;
  }
  .brand-dot {
    width: 14px; height: 14px; border-radius: 50%; background: var(--brand-red);
  }
  .back-brand .brand-name {
    color: var(--white); font-size: 22px; font-weight: 700; letter-spacing: .5px;
  }
  .back-web {
    position: absolute; right: 40px; top: 160px;
    color: #cfcfcf; font-size: 12px; letter-spacing: .4px;
  }

  /* Front side */
  .card--front { background: var(--paper); }
  .front-brand {
    position: absolute; left: 38px; top: 118px;
    display: flex; align-items: center; gap: 10px;
  }
  .front-brand .brand-name {
    color: var(--ink); font-size: 22px; font-weight: 700; letter-spacing: .5px;
  }
  .edge-accent {
    position: absolute; right: -16px; top: 84px;
    width: 32px; height: 32px; border-radius: 50%; background: var(--brand-red);
  }
  .contact {
    position: absolute; right: 38px; top: 74px; text-align: right;
  }
  .contact .person-name {
    color: var(--brand-red); font-size: 16px; font-weight: 700; letter-spacing: 1px;
  }
  .contact .person-role {
    color: var(--ink); font-size: 12px; margin-bottom: 14px;
  }
  .contact .address {
    color: var(--ink-soft); font-size: 11.5px; line-height: 1.45; margin-bottom: 10px;
  }
  .contact-list { list-style: none; }
  .contact-list li {
    display: flex; justify-content: flex-end; align-items: center; gap: 8px;
    color: var(--ink-soft); font-size: 11.5px; line-height: 1.75;
  }
  .contact-list svg { width: 12px; height: 12px; fill: var(--brand-red); flex: none; }
</style>
</head>
<body>
<main class="stage">

  <section class="card card--back" aria-label="Business card, back">
    <div class="back-pattern" role="img" aria-label="Repeating brand pattern in dark tones"></div>
    <div class="back-brand">
      <span class="brand-dot"></span>
      <span class="brand-name">Lorno Productions</span>
    </div>
    <p class="back-web">www.lornohub.com</p>
  </section>

  <section class="card card--front" aria-label="Business card, front">
    <div class="front-brand">
      <span class="brand-dot"></span>
      <span class="brand-name">Lorno Productions</span>
    </div>
    <span class="edge-accent"></span>

    <div class="contact">
      <p class="person-name">DANIEL KOH</p>
      <p class="person-role">CEO/Founder</p>
      <p class="address">2146 Willow Crest Lane<br>Fairbanks, Alaska 99701</p>
      <ul class="contact-list">
        <li>612 408 3175
          <svg viewBox="0 0 24 24" aria-label="Phone"><path d="M6.6 10.8a15 15 0 0 0 6.6 6.6l2.2-2.2a1 1 0 0 1 1-.25 11.4 11.4 0 0 0 3.6.57 1 1 0 0 1 1 1V20a1 1 0 0 1-1 1A17 17 0 0 1 3 4a1 1 0 0 1 1-1h3.5a1 1 0 0 1 1 1c0 1.25.2 2.45.57 3.57a1 1 0 0 1-.25 1z"/></svg>
        </li>
        <li>847 215 6390
          <svg viewBox="0 0 24 24" aria-label="Mobile"><path d="M7 1h10a2 2 0 0 1 2 2v18a2 2 0 0 1-2 2H7a2 2 0 0 1-2-2V3a2 2 0 0 1 2-2zm0 3v15h10V4zm5 16.2a.9.9 0 1 0 0 1.8.9.9 0 0 0 0-1.8z"/></svg>
        </li>
        <li>493 702 8156
          <svg viewBox="0 0 24 24" aria-label="Fax"><path d="M7 2h10v5H7zM4 8h16a2 2 0 0 1 2 2v7h-4v5H6v-5H2v-7a2 2 0 0 1 2-2zm4 8v4h8v-4z"/></svg>
        </li>
        <li>name@lornohub.com
          <svg viewBox="0 0 24 24" aria-label="Email"><path d="M2 5h20v14H2zm2 2v.4l8 5.1 8-5.1V7zm0 2.8V17h16V9.8l-8 5.1z"/></svg>
        </li>
        <li>www.lornohub.com
          <svg viewBox="0 0 24 24" aria-label="Website"><path d="M12 2a10 10 0 1 0 0 20 10 10 0 0 0 0-20zm6.9 6h-3a15 15 0 0 0-1.3-3.8A8 8 0 0 1 18.9 8zM12 4c.8 1.1 1.5 2.5 1.9 4h-3.8c.4-1.5 1.1-2.9 1.9-4zM4.3 14a8 8 0 0 1 0-4h3.3a16 16 0 0 0 0 4zm.8 2h3a15 15 0 0 0 1.3 3.8A8 8 0 0 1 5.1 16zm3-8h-3a8 8 0 0 1 4.3-3.8A15 15 0 0 0 8.1 8zM12 20c-.8-1.1-1.5-2.5-1.9-4h3.8c-.4 1.5-1.1 2.9-1.9 4zm2.3-6H9.7a14 14 0 0 1 0-4h4.6a14 14 0 0 1 0 4zm.3 5.8a15 15 0 0 0 1.3-3.8h3a8 8 0 0 1-4.3 3.8zm1.8-5.8a16 16 0 0 0 0-4h3.3a8 8 0 0 1 0 4z"/></svg>
        </li>
      </ul>
    </div>
  </section>

</main>
</body>
</html>
```